Halvor Grading and Septic needs a flyer to submit to contractors to offer our services

I need a sleek profession one page full color high gloss document showcasing our services to give to Mobile Home Companies and contractors that need our services.

Target Market(s)

Home Builders. Mobile Home Salesmen. People Building new homes.

Industry/Entity Type

Construction

Font styles to use
Serif
Sans Serif

Requirements
Must have
• Phone Number. Email address. Logo. Services offered: Mobile Home Pads, Meter Pole Placement and Connection, Waterline Connection, On Site Septic System Installs
Should not have
• Jokes, Nothing trying to be cute

```html
<!DOCTYPE html>
<html lang="en">
<head>
<meta charset="utf-8">
<title>Halvor Grading and Septic – Services Flyer</title>
<link href="https://fonts.googleapis.com/css2?family=Montserrat:ital,wght@0,600;0,700;0,800;1,500;1,700;1,800;1,900&display=swap" rel="stylesheet">
<style>
  :root{
    --navy:#1b4f8c;
    --blue:#1d5796;
    --blue-deep:#174a82;
    --red:#cc1f2a;
    --red-dark:#a8141d;
    --white:#ffffff;
  }
  *{margin:0;padding:0;box-sizing:border-box}
  html,body{width:803px;height:1200px;overflow:hidden;background:#ffffff}
  body{font-family:"Montserrat",Arial,sans-serif}
  .flyer{position:relative;width:803px;height:1200px;overflow:hidden;background:var(--blue)}
  .flyer-art{position:absolute;inset:0}
  .brand{position:absolute;left:34px;top:40px;width:290px;display:flex;align-items:center;gap:10px}
  .brand-mark{width:22px;height:22px;background:var(--navy);flex:none}
  .brand-name{font-weight:800;font-size:22px;line-height:1.05;color:var(--navy);text-transform:uppercase}
  .headline{position:absolute;left:0;width:803px;text-align:center;font-style:italic;font-weight:900;text-transform:uppercase;line-height:1}
  .headline-top{top:206px;font-size:40px;color:var(--white);letter-spacing:1px;left:-10px}
  .headline-main{top:248px;font-size:71px;color:var(--red);left:5px}
  .headline-bottom{top:324px;font-size:53px;color:var(--white);left:-15px}
  .intro{position:absolute;left:150px;width:480px;top:421px;text-align:center;color:var(--white)}
  .intro-text{font-style:italic;font-weight:500;font-size:14px;line-height:1.25}
  .intro-cta{font-style:italic;font-weight:700;font-size:19.5px;margin-top:12px}
  .services-title{position:absolute;left:215px;top:561px;width:372px;height:39px;border-radius:20px;background:var(--red);color:var(--white);font-style:italic;font-weight:800;font-size:30px;text-align:center;line-height:39px}
  .service{position:absolute;width:340px;text-align:center;color:var(--white)}
  .service-icon{display:block;margin:0 auto 12px;width:96px;height:96px}
  .service-label{font-weight:600;font-size:20px;line-height:1.25;text-transform:uppercase}
  .service--pads{left:30px;top:632px}
  .service--meter{left:382px;top:632px}
  .service--water{left:30px;top:820px}
  .service--septic{left:382px;top:820px}
  .contact{position:absolute;color:var(--white);font-style:italic;font-weight:700}
  .contact-email{left:20px;width:480px;top:1127px;text-align:center;font-size:18px}
  .contact-phone{left:478px;width:320px;top:1118px;text-align:center;font-size:33px;font-weight:800}
</style>
</head>
<body>
<main class="flyer">
  <svg class="flyer-art" viewBox="0 0 803 1200" width="803" height="1200">
    <defs>
      <linearGradient id="siteGrad" x1="0" y1="0" x2="0" y2="1">
        <stop offset="0" stop-color="#7e8f6a"/>
        <stop offset="0.35" stop-color="#a58c66"/>
        <stop offset="0.75" stop-color="#6f7f98"/>
        <stop offset="1" stop-color="#3f6797"/>
      </linearGradient>
      <linearGradient id="bodyGrad" x1="0" y1="0" x2="0" y2="1">
        <stop offset="0" stop-color="#1a5190"/>
        <stop offset="1" stop-color="#2360a1"/>
      </linearGradient>
      <radialGradient id="tankGrad" cx="0.7" cy="0.6" r="0.7">
        <stop offset="0" stop-color="#4a80b8" stop-opacity="0.45"/>
        <stop offset="0.6" stop-color="#3b74b0" stop-opacity="0.2"/>
        <stop offset="1" stop-color="#2360a1" stop-opacity="0"/>
      </radialGradient>
      <linearGradient id="panelGrad" x1="0" y1="0" x2="0" y2="1">
        <stop offset="0" stop-color="#6c7c96"/>
        <stop offset="1" stop-color="#255c9a"/>
      </linearGradient>
    </defs>

    <rect x="0" y="0" width="803" height="1200" fill="url(#bodyGrad)"/>

    <rect x="0" y="40" width="803" height="370" fill="url(#siteGrad)" role="img" aria-label="Photo of an excavator digging beside a freshly installed septic system on a rural lot"/>

    <rect x="300" y="840" width="503" height="330" fill="url(#tankGrad)" role="img" aria-label="Faded photo of a crew setting a concrete septic tank"/>

    <polygon points="0,146 332,146 360,28 803,28 803,50 378,50 348,162 0,162" fill="var(--navy)"/>
    <polygon points="0,0 803,0 803,28 360,28 332,146 0,146" fill="var(--white)"/>

    <rect x="0" y="404" width="803" height="5" fill="var(--white)"/>
    <polygon points="30,409 762,409 650,540 76,540" fill="var(--red)"/>
    <polygon points="134,409 661,409 628,526 114,526" fill="url(#panelGrad)" stroke="var(--white)" stroke-width="4"/>

    <polygon points="0,1058 492,1058 460,1170 803,1170 803,1200 0,1200" fill="var(--red)"/>
    <polyline points="0,1056 492,1056 461,1168 803,1168" fill="none" stroke="var(--white)" stroke-width="4"/>

    <circle cx="255" cy="1091" r="18" fill="var(--white)"/>
    <rect x="245" y="1084" width="20" height="14" rx="1.5" fill="none" stroke="var(--red)" stroke-width="2"/>
    <polyline points="245,1085 255,1093 265,1085" fill="none" stroke="var(--red)" stroke-width="2"/>

    <circle cx="639" cy="1087" r="16" fill="var(--red)"/>
    <path d="M632 1080 q-2 2 0 6 q4 7 11 10 q3 1 5 -1 l-3 -4 l-3 2 q-4 -2 -6 -6 l2 -3 z" fill="var(--white)"/>
  </svg>

  <div class="brand">
    <span class="brand-mark"></span>
    <span class="brand-name">Halvor Grading &amp; Septic</span>
  </div>

  <h1>
    <span class="headline headline-top">Professional</span>
    <span class="headline headline-main">Wastewater</span>
    <span class="headline headline-bottom">Management</span>
  </h1>

  <div class="intro">
    <p class="intro-text">Halvor Grading and Septic offers professional septic and excavation services in East Texas.</p>
    <p class="intro-cta">Call us now for a free estimate!</p>
  </div>

  <h2 class="services-title">Services offered:</h2>

  <div class="service service--pads">
    <svg class="service-icon" viewBox="0 0 96 96" aria-hidden="true">
      <circle cx="48" cy="48" r="45" fill="var(--red)" stroke="#7e9ac0" stroke-width="4"/>
      <polygon points="26,44 48,28 70,44" fill="none" stroke="#fff" stroke-width="3"/>
      <rect x="30" y="44" width="36" height="18" fill="none" stroke="#fff" stroke-width="3"/>
      <rect x="36" y="48" width="9" height="8" fill="#fff"/>
      <rect x="52" y="48" width="8" height="14" fill="#fff"/>
      <circle cx="38" cy="67" r="3.5" fill="none" stroke="#fff" stroke-width="2.5"/>
      <circle cx="47" cy="67" r="3.5" fill="none" stroke="#fff" stroke-width="2.5"/>
      <line x1="66" y1="62" x2="72" y2="66" stroke="#fff" stroke-width="3"/>
    </svg>
    <p class="service-label">Mobile<br>Home Pads</p>
  </div>

  <div class="service service--meter">
    <svg class="service-icon" viewBox="0 0 96 96" aria-hidden="true">
      <circle cx="48" cy="48" r="45" fill="var(--red)" stroke="#7e9ac0" stroke-width="4"/>
      <line x1="36" y1="24" x2="36" y2="64" stroke="#fff" stroke-width="3"/>
      <line x1="26" y1="30" x2="46" y2="30" stroke="#fff" stroke-width="3"/>
      <line x1="28" y1="37" x2="44" y2="37" stroke="#fff" stroke-width="3"/>
      <rect x="50" y="48" width="22" height="16" rx="2" fill="none" stroke="#fff" stroke-width="3"/>
      <circle cx="57" cy="56" r="3" fill="#fff"/>
      <line x1="63" y1="53" x2="68" y2="53" stroke="#fff" stroke-width="2"/>
      <line x1="63" y1="58" x2="68" y2="58" stroke="#fff" stroke-width="2"/>
      <path d="M52 30 q10 0 10 10 l-3 -3 m3 3 l3 -3" fill="none" stroke="#fff" stroke-width="2.5"/>
      <path d="M44 70 q-10 0 -10 -6" fill="none" stroke="#fff" stroke-width="2.5"/>
    </svg>
    <p class="service-label">Meter Pole Placement<br>and Connection</p>
  </div>

  <div class="service service--water">
    <svg class="service-icon" viewBox="0 0 96 96" aria-hidden="true">
      <circle cx="48" cy="48" r="45" fill="var(--red)" stroke="#7e9ac0" stroke-width="4"/>
      <polygon points="28,40 48,26 68,40" fill="none" stroke="#fff" stroke-width="3"/>
      <path d="M34 46 h14 v8 h10 v12" fill="none" stroke="#fff" stroke-width="5"/>
      <path d="M40 66 v-8 h-8" fill="none" stroke="#fff" stroke-width="5"/>
      <rect x="52" y="66" width="14" height="6" fill="#fff"/>
    </svg>
    <p class="service-label">Waterline<br>Connection</p>
  </div>

  <div class="service service--septic">
    <svg class="service-icon" viewBox="0 0 96 96" aria-hidden="true">
      <circle cx="48" cy="48" r="45" fill="var(--red)" stroke="#7e9ac0" stroke-width="4"/>
      <rect x="26" y="40" width="44" height="26" rx="5" fill="#fff"/>
      <rect x="34" y="30" width="10" height="10" fill="#fff"/>
      <rect x="52" y="30" width="10" height="10" fill="#fff"/>
      <rect x="32" y="28" width="14" height="3" fill="#fff"/>
      <rect x="50" y="28" width="14" height="3" fill="#fff"/>
      <line x1="48" y1="44" x2="48" y2="66" stroke="var(--red)" stroke-width="3"/>
    </svg>
    <p class="service-label">On Site Septic<br>System Installs</p>
  </div>

  <p class="contact contact-email">owen@halvorgradingandseptic.com</p>
  <p class="contact contact-phone">(555) 214-0388</p>
</main>
</body>
</html>
```